Klassisches Visitenkarten-Design mit braunen Farbtönen gesucht
Zielgruppe
Meine Firma bietet Pferdezahnbehandlungen, Pferdefütterungsberatung sowie Trensen- und Gebissanpassungen an. Ausserdem habe ich eine mobile Pferdewaage. Meine Kunden sind Pferdebesitzer der gehobenen Klasse, die gerne Geld in die Hand nehmen um ihr Tier korrekt zu halten/versorgen.
Ich setze bisher auf ein klassisches Design in braun Tönen.
Aufgabenstellung
Mir ist eine klare, schnörkellose Botschaft wichtig.
Ich möchte mich gerne mit klassischem, aber auch sehr schönem Design von der Konkurrenz abheben.
Der Fokus soll auf der wissenschaftlichen Arbeitsweise mit dem Partner Pferd liegen.
Im Anhang sind Fotos von der alten Visitenkarten. Dort fehlt mir aber die klare Linie.
Normalerweise arbeite ich mit der Schriftart Eurostyle, bin aber auch für neue Vorschläge offen.

```html
<!DOCTYPE html>
<html lang="de">
<head>
<meta charset="utf-8">
<title>Visitenkarte EQUIVIA</title>
<link href="https://fonts.googleapis.com/css2?family=Saira:wght@400;600&display=swap" rel="stylesheet">
<style>
  :root {
    --stage: #ededed;
    --card-white: #ffffff;
    --brown-deep: #542d12;
    --text-grey: #6e6e6e;
    --shadow-light: #b3b4bb;
    --shadow-dark: #757b83;
  }
  html, body {
    margin: 0;
    padding: 0;
    width: 1200px;
    height: 1200px;
    overflow: hidden;
    background: var(--stage);
    font-family: "Saira", "Helvetica Neue", Arial, sans-serif;
  }
  .stage { position: relative; width: 1200px; height: 1200px; }
  .card {
    position: absolute;
    left: 238px;
    width: 723px;
    height: 468px;
  }
  .card--front { top: 80px; background: var(--card-white); }
  .card--back { top: 643px; background: var(--brown-deep); }
  .card-shadow {
    position: absolute;
    left: 248px;
    width: 723px;
    height: 468px;
    background: linear-gradient(120deg, var(--shadow-light), var(--shadow-dark));
  }
  .card-shadow--front { top: 90px; }
  .card-shadow--back { top: 653px; }

  .contact {
    position: absolute;
    left: 46px;
    top: 112px;
    color: var(--text-grey);
    font-size: 18.5px;
    line-height: 22.5px;
  }
  .contact p { margin: 0; }
  .contact .name,
  .contact .title,
  .contact .company { font-weight: 600; font-size: 17.5px; }
  .contact .title { margin-top: 22px; }
  .contact .address { margin-top: 18px; }
  .contact .channels { margin-top: 22px; }
  .channel-row { display: flex; }
  .channel-row .label { width: 84px; }

  .services {
    position: absolute;
    left: 0;
    right: 0;
    top: 399px;
    text-align: center;
    color: var(--text-grey);
    font-weight: 600;
    font-size: 18px;
    letter-spacing: 0.1px;
  }

  .brand {
    position: absolute;
    display: flex;
    align-items: center;
    gap: 12px;
    font-weight: 600;
    letter-spacing: 2px;
  }
  .brand--front {
    left: 470px;
    top: 150px;
    color: var(--brown-deep);
    font-size: 36px;
  }
  .brand--back {
    left: 0;
    right: 0;
    top: 200px;
    justify-content: center;
    color: var(--card-white);
    font-size: 52px;
  }
  .brand-dot { border-radius: 50%; background: currentColor; }
  .brand--front .brand-dot { width: 16px; height: 16px; }
  .brand--back .brand-dot { width: 22px; height: 22px; }
</style>
</head>
<body>
<main class="stage">
  <div class="card-shadow card-shadow--front"></div>
  <section class="card card--front" aria-label="Vorderseite">
    <div class="contact">
      <p class="name">Marlene T. Hausner</p>
      <p class="title">Agrarwissenschaften (Dr. sc.)</p>
      <p class="company">EQUIVIA</p>
      <div class="address">
        <p>Lindenweg 12</p>
        <p>79199 Talheim/Südschwarzwald</p>
      </div>
      <div class="channels">
        <p class="channel-row"><span class="label">Telefon:</span><span>+49 (0) 160 - 5550183</span></p>
        <p class="channel-row"><span class="label">E-Mail:</span><span>praxis@equivia-pferd.de</span></p>
        <p class="channel-row"><span class="label">Internet:</span><span>www.equivia-pferd.de</span></p>
      </div>
    </div>
    <div class="brand brand--front"><span class="brand-dot"></span><span>EQUIVIA</span></div>
    <p class="services">Pferdezahnbehandlung&nbsp; *&nbsp; Pferdefütterungsberatung&nbsp; *&nbsp; Pferdewaage</p>
  </section>

  <div class="card-shadow card-shadow--back"></div>
  <section class="card card--back" aria-label="Rückseite">
    <div class="brand brand--back"><span class="brand-dot"></span><span>EQUIVIA</span></div>
  </section>
</main>
</body>
</html>
```